verdant terraces simple classy business card design

my name is colin barrow and I run a gardening business aimed at high class verdant terraces. the business name is verdant terraces and our logo was designed on pixel harbour .My clientel are anything from residential homes to businesses. I take pride in my work and know that I offer a service like no other in my area.
The business card will be used to represent my business and I want it to be not only rememberable, but simplistic and modern. Eye catching too. Of course I would like it relatable to gardening and appealing to the correct clientel - those being garden enthusiasts, prestigious homes and businesses that are after top of the line gardening services like no other on the market.
I am not a typical lawn mowing business so I don't want a typical card design that represents that. The gardens I work with are generally million dollar properties with owners who are very garden proud looking for upkeep and guidance from me along with sometimes whole new garden designs. I want the business cards to show to my clients that I take pride, as they do, in their garden. And I want them to know from my card that I am a professional, qualified horticulturist offering them a top of the line service for life. I want them to refer my business on. I want them to look at my business card and see class and professionalism in a modern unique bold way.
The card should be simple with the possibility of the logo on the front being embossed/debossed and my details on the back the card should have a organic garden feel it's very important to me that it is absolutely perfect
I am also very open to ideas and suggestions so look forward to seeing the designs. the business logo has been supplied with this project and I want the card to be double sided

Contact info is
Colin Barrow - Managing Director / Horticulturist
Phone : 0481 526 704
Email: colinbarrow@verdantterraces.example.au

Target Market(s)

high class gardens residential and commercial

Industry/Entity Type

Gardener

Contact Information for Business Card

Contact info is
Phone : 0481 526 704

PLEASE MAKE CARD DOUBLE SIDED

Requirements
Must have
• organic simple classy modern feel
• must flow with the current logo that has been supplied with this project
• Double sided
• Must explain in a simple way that I deal with high end gardens and I'm a qualified horticulturist
Nice to have
• embossed debossed logo
Should not have
• shouldn't be to busy or cheap looking

```html
<!DOCTYPE html>
<html lang="en">
<head>
<meta charset="utf-8">
<title>Verdant Terraces – Business Card</title>
<link href="https://fonts.googleapis.com/css2?family=Source+Sans+3:wght@400;600&display=swap" rel="stylesheet">
<style>
  :root {
    --bg-top: #a6a6a6;
    --bg-bottom: #878787;
    --card-light: #f3f3f3;
    --card-dark: #252525;
    --leaf-green: #4f8d3f;
    --brand-green: #5a9a46;
    --text-grey: #555555;
  }
  * { margin: 0; padding: 0; box-sizing: border-box; }
  html, body {
    width: 1200px;
    height: 900px;
    overflow: hidden;
  }
  body {
    position: relative;
    background: linear-gradient(180deg, var(--bg-top) 0%, var(--bg-bottom) 100%);
    font-family: "Source Sans 3", "Myriad Pro", Arial, sans-serif;
  }
  .card {
    position: absolute;
    top: 184px;
    height: 490px;
    border-radius: 14px;
  }
  .card--front {
    left: 299px;
    width: 301px;
    background: var(--card-light);
  }
  .card--back {
    left: 645px;
    width: 305px;
    background: var(--card-dark);
  }
  .brand-mark {
    position: absolute;
    left: 50%;
    transform: translateX(-50%);
    border-radius: 50%;
    background: var(--leaf-green);
  }
  .card--front .brand-mark {
    top: 58px;
    width: 118px;
    height: 118px;
  }
  .card--back .brand-mark {
    top: 298px;
    width: 70px;
    height: 70px;
    background: var(--brand-green);
  }
  .brand-name {
    position: absolute;
    left: 0;
    right: 0;
    text-align: center;
    text-transform: uppercase;
    font-weight: 400;
    letter-spacing: 0.14em;
  }
  .card--front .brand-name {
    top: 196px;
    font-size: 17px;
    line-height: 22px;
    color: var(--leaf-green);
  }
  .card--back .brand-name {
    top: 376px;
    font-size: 27px;
    line-height: 31px;
    color: var(--brand-green);
  }
  .contact {
    position: absolute;
    top: 282px;
    left: 0;
    right: 0;
    text-align: center;
    color: var(--text-grey);
    font-size: 13px;
    line-height: 17.5px;
  }
  .contact__name {
    font-size: 17px;
    line-height: 20px;
    font-weight: 600;
    color: var(--leaf-green);
  }
  .contact__role { margin-bottom: 12px; }
  .contact__address { margin-bottom: 13px; }
  .contact__email { font-size: 12px; }
</style>
</head>
<body>
  <section class="card card--front" aria-label="Card front">
    <div class="brand-mark"></div>
    <div class="brand-name">Verdant Terraces</div>
    <div class="contact">
      <p class="contact__name">Colin Barrow</p>
      <p class="contact__role">Managing Director</p>
      <p class="contact__address">18 Fernleigh Rise<br>Hawthorn Vale, 3122.</p>
      <p class="contact__phone">0481 526 704</p>
      <p class="contact__email">colinbarrow@verdantterraces.example.au</p>
      <p class="contact__web">www.verdantterraces.example.au</p>
    </div>
  </section>

  <section class="card card--back" aria-label="Card back">
    <div class="brand-mark"></div>
    <div class="brand-name">Verdant<br>Terraces</div>
  </section>
</body>
</html>
```